Landscape design build company door flyer

I would like this flyer to convey a high-level of professionalism for a company that is excellent with communication with their clients as well as a company that does incredible installations

Went on vacation/holiday

```html
<!DOCTYPE html>
<html lang="en">
<head>
<meta charset="utf-8">
<title>Cedarline Builders – Outdoor Living Flyer</title>
<link href="https://fonts.googleapis.com/css2?family=Montserrat:wght@300;400;600;700;800&family=Roboto+Condensed:wght@700&display=swap" rel="stylesheet">
<style>
  :root{
    --ink:#10283d;
    --navy:#0d2a40;
    --navy-glow:#1c5473;
    --rule:#b9bec4;
    --paper:#ffffff;
    --backdrop:#e4e4e4;
  }
  html,body{margin:0;padding:0;width:1200px;height:1029px;overflow:hidden;background:var(--backdrop);}
  body{font-family:"Montserrat",sans-serif;color:var(--ink);position:relative;}
  .flyer{position:absolute;left:241px;top:53px;width:717px;height:922px;background:var(--paper);overflow:hidden;}

  .brand{position:absolute;left:0;width:307px;top:104px;text-align:center;}
  .brand-name{font-family:"Montserrat",sans-serif;font-weight:700;font-size:17px;letter-spacing:.5px;color:var(--ink);display:inline-flex;align-items:center;gap:8px;}
  .brand-mark{width:12px;height:12px;background:var(--ink);display:inline-block;}

  .headline{position:absolute;left:36px;top:172px;margin:0;font-family:"Roboto Condensed",sans-serif;font-weight:700;font-size:36.5px;line-height:34px;color:var(--ink);text-transform:uppercase;}

  .divider{position:absolute;left:36px;top:325px;width:239px;height:1px;background:var(--rule);}
  .divider::before{content:"";position:absolute;left:0;top:-1px;width:116px;height:3px;background:var(--ink);}

  .intro{position:absolute;left:36px;top:341px;width:239px;margin:0;font-size:11.2px;font-weight:400;line-height:13.7px;text-align:justify;color:var(--ink);}

  .services{position:absolute;left:38px;top:440px;margin:0;padding:0;list-style:none;}
  .services li{height:32px;display:flex;align-items:center;font-weight:700;font-size:15px;letter-spacing:.2px;}
  .services li::before{content:"";width:2px;height:18px;background:var(--ink);margin-right:7px;}

  .contact-panel{position:absolute;left:0;top:672px;width:307px;height:250px;background:radial-gradient(ellipse 180px 150px at 50% 55%,var(--navy-glow),var(--navy));color:#fff;}
  .areas{position:absolute;left:36px;top:15px;width:250px;margin:0;font-size:11.2px;font-weight:400;line-height:17px;}
  .areas strong{font-weight:600;}
  .contact-tag{position:absolute;left:36px;top:97px;width:270px;height:21px;}
  .contact-tag svg{position:absolute;left:0;top:0;}
  .contact-tag span{position:absolute;left:7px;top:2px;font-weight:800;font-size:13.5px;letter-spacing:4.6px;color:var(--ink);}
  .phone{position:absolute;left:36px;top:128px;display:flex;align-items:center;gap:12px;font-weight:700;font-size:24px;letter-spacing:3.4px;}
  .line-item{position:absolute;left:40px;display:flex;align-items:center;gap:14px;font-size:11.6px;font-weight:400;}
  .email{top:166px;}
  .web{top:187px;}

  .photo{position:absolute;left:310px;width:407px;}
  .photo-deck{top:0;height:228px;background:linear-gradient(160deg,#5e8a3c 0%,#3f6e2c 35%,#9a4a2a 60%,#7a3a22 100%);}
  .photo-driveway{top:232px;height:227px;background:linear-gradient(180deg,#6f7a72 0%,#4f6b3a 40%,#5c4a38 75%,#4a5a3a 100%);}
  .photo-pool{top:464px;height:226px;background:linear-gradient(180deg,#c9d6dc 0%,#e8ece9 35%,#7fa56a 60%,#5fc6bf 100%);}
  .photo-pavilion{top:695px;height:227px;background:linear-gradient(180deg,#b07a4a 0%,#3c3a36 35%,#6a6e74 70%,#56606c 100%);}
</style>
</head>
<body>
  <main class="flyer">
    <div class="brand"><span class="brand-name"><span class="brand-mark"></span>CEDARLINE BUILDERS</span></div>

    <h1 class="headline">Let’s create<br>your dream<br>outdoor<br>living space!</h1>

    <div class="divider"></div>

    <p class="intro">Discover the endless possibilities for your outdoor space with The Cedarline Builders Team. Our team of skilled artisans is dedicated to turning your outdoor space into a breathtaking oasis that you’ll love coming home to. Our services include:</p>

    <ul class="services">
      <li>PAVER PATIOS</li>
      <li>PAVER DRIVEWAYS</li>
      <li>RETAINING WALLS</li>
      <li>DECKS &amp; RAILINGS</li>
      <li>POOLS</li>
      <li>OUTDOOR LIGHTING</li>
      <li>FIREPITS &amp; FIREPLACES</li>
    </ul>

    <section class="contact-panel">
      <p class="areas">Our service areas include <strong>Bellevue, Issaquah, Kirkland, Redmond, and Sammamish</strong>. We are trusted, tested and reliable with over 20-years experiences.</p>

      <div class="contact-tag">
        <svg width="234" height="21" viewBox="0 0 234 21">
          <path d="M0 0H150L158 10.5L150 21H0Z" fill="#fff"/>
          <line x1="156" y1="10.5" x2="234" y2="10.5" stroke="#c8d0d6" stroke-width="1"/>
        </svg>
        <span>CONTACT US</span>
      </div>

      <div class="phone">
        <svg width="20" height="22" viewBox="0 0 24 24"><path fill="#fff" d="M6.6 2.2c.6-.3 1.3-.1 1.6.5l2 3.8c.3.6.2 1.3-.3 1.7L8.4 9.5c1.1 2.5 3.3 4.9 6 6.1l1.4-1.5c.4-.5 1.1-.6 1.7-.3l3.8 2c.6.3.8 1 .5 1.6l-1.2 2.4c-.4.8-1.3 1.3-2.2 1.1C10.2 19.4 4.5 13.6 3 5.4c-.2-.9.3-1.8 1.1-2.2z"/></svg>
        206-555-0148
      </div>

      <div class="line-item email">
        <svg width="14" height="10" viewBox="0 0 14 10"><rect x="0.5" y="0.5" width="13" height="9" fill="none" stroke="#fff"/><path d="M0.5 0.5L7 6L13.5 0.5" fill="none" stroke="#fff"/></svg>
        info@cedarlinebuilders.com
      </div>
      <div class="line-item web">
        <svg width="13" height="13" viewBox="0 0 14 14"><g fill="none" stroke="#fff" stroke-width="1"><circle cx="7" cy="7" r="6"/><ellipse cx="7" cy="7" rx="2.6" ry="6"/><line x1="1" y1="7" x2="13" y2="7"/></g></svg>
        www.cedarlinebuilders.com
      </div>
    </section>

    <div class="photo photo-deck" role="img" aria-label="Photo of a wooden deck with a pergola and red patio chairs among trees"></div>
    <div class="photo photo-driveway" role="img" aria-label="Aerial photo of a house with a paver driveway, walkway and landscaped beds"></div>
    <div class="photo photo-pool" role="img" aria-label="Photo of a modern house with a covered terrace and a turquoise pool"></div>
    <div class="photo photo-pavilion" role="img" aria-label="Photo of a timber pavilion with a stacked stone fireplace and outdoor kitchen"></div>
  </main>
</body>
</html>
```